Wordpress Web Design & Coding for velcorahealth.ca

We need a website for a new investment company that is visually grabbing and vibrant. We would like to see a web page that displays trust, growth and confidence. Needs to be responsive and mobile friendly for all browsers and coded for both Android & IOS.

Open to the number of pages and menu items. I selected 4 but if you feel the layout would work better with less I am open to this. Need to sell the people (management team/related businesses) and then show where the invested money will be going (upcoming projects).

Company Info:

Vel Cora is an investment company put together by a group of seasoned business professionals who have come together to combine decades of success in the real estate development, management, financing and medical services. The company will be a full service company offering turn key solutions for medical professionals.

Vel-Cora will focus on providing a full range of services via a group of distinct companies to deliver newly emerging needs of the medical community. The end goal will be to create complete solutions for individuals in the medical community. Our group has experience and success with the conceptualization, construction and financing of medical and dental clinic spaces. Vel-Cora Solutions will be established to accommodate all areas of the development and creation of clinics for medical professionals from building construction to equipment financing and administrations.

You can mention these companies and take photos from their websites. You can also use stock photos.

Our construction partner:
https://318bld.com/projects/

Our equipment leasing partner:
https://www.norvixa.com/

Our Management Team and medical partners

Gil Parish
https://www.ourfirmstance.ca/

Dietmar Vellasquin
https://www.gshdentalservices.com/about-us

PROPOSED PROJECTS (see attachment for details)
Pinegrove Business Park
Holtmere Business Park
Mt. Corwin Ridge Professional

Target Market(s)

Investors

Industry/Entity Type

Investment

Coding

Coded - Design and coding required

Number of Pages Required

4 page

Font styles to use
Sans Serif

Requirements
Must have
• Wordpress – must be both desktop and mobile friendly with fast page load speed
Ability to edit after ourselves in Wordpress
Attractive home page with logo etc.
Logo colours are: for the blue the pantone color is #0355a3
and for the green is #8cc63f

Sections, about us, what we do/services we provide, contact us

```html
<!DOCTYPE html>
<html lang="en">
<head>
<meta charset="utf-8">
<title>Vel-Cora Solutions</title>
<link rel="stylesheet" href="https://fonts.googleapis.com/css2?family=Poppins:wght@400;500;600&family=Roboto+Condensed:wght@400&display=swap">
<style>
:root{
  --blue:#0355a3;
  --blue-mid:#1a6fc0;
  --green:#8cc63f;
  --ink:#222831;
  --muted:#3c4450;
  --tint:#eef3f9;
  --white:#ffffff;
}
*{box-sizing:border-box;margin:0;padding:0}
html,body{width:1200px;height:3579px;overflow:hidden}
body{font-family:"Poppins",sans-serif;color:var(--ink);background:var(--white)}
.page{position:relative;width:1200px;height:3579px;overflow:hidden}
.abs{position:absolute}
.band{position:absolute;left:0;width:1200px}
.title{position:absolute;left:0;width:1200px;text-align:center;font-size:32px;font-weight:400;color:var(--blue);line-height:1.2}
.title .accent{color:var(--green)}
.title-rule{position:absolute;left:581px;width:38px;height:2px;background:#555d68}
.hero-bg{top:0;height:564px;background:linear-gradient(180deg,#9db4c9 0%,#8a8f86 35%,#6b645c 65%,#3a3a3c 100%)}
.hero-shade{top:380px;height:184px;background:linear-gradient(180deg,rgba(20,24,30,0),rgba(20,24,30,.75))}
.topbar{font-size:15px;color:var(--ink);display:flex;align-items:center;gap:10px}
.nav a{position:absolute;font-size:17px;color:var(--ink);text-decoration:none}
.nav a.active{color:var(--blue);font-weight:500}
.badge{position:absolute;background:var(--white);display:flex;flex-direction:column;align-items:center;justify-content:center;clip-path:polygon(0 0,100% 0,100% 78%,50% 100%,0 78%)}
.brand{font-weight:600;color:var(--blue);font-size:36px;line-height:1;letter-spacing:.5px;text-align:center}
.brand-sub{font-weight:600;color:var(--blue);font-size:22px;line-height:1.2;letter-spacing:1px}
.hero-text{top:448px;left:0;width:1200px;text-align:center;font-family:"Roboto Condensed",sans-serif;font-weight:400;color:var(--white);font-size:38px;line-height:54px}
.about-text{left:160px;width:880px;text-align:center;font-size:13px;line-height:23px;color:var(--muted)}
.about-text p{margin-bottom:8px}
.btn{position:absolute;height:34px;background:var(--blue);color:var(--white);font-size:15px;font-weight:500;display:flex;align-items:center;gap:10px;padding:0 10px 0 0}
.btn .mark{width:26px;height:34px;background:var(--green);margin-left:-10px}
.sol-col{width:285px}
.sol-icon{width:76px;height:76px;border-radius:50%;border:2px solid var(--blue);background:var(--white);display:flex;align-items:center;justify-content:center}
.sol-col h3{font-size:18px;font-weight:500;color:var(--blue);margin:16px 0 10px}
.sol-col p{font-size:13px;line-height:23px;color:var(--muted)}
.sol-col a{display:inline-block;margin-top:12px;font-size:14px;color:var(--green);text-decoration:underline}
.sol-mark{background:var(--blue);display:flex;align-items:center;justify-content:center}
.member{width:280px;text-align:center}
.portrait{width:182px;height:182px;border-radius:50%;background:radial-gradient(circle at 50% 40%,#2f86d6,var(--blue));margin:0 auto}
.member h4{font-size:18px;font-weight:500;margin-top:30px;color:var(--ink)}
.firm{margin-top:14px;font-size:24px;font-weight:400;color:var(--ink);line-height:1.2}
.project{position:absolute;width:441px;height:318px;overflow:hidden}
.project .cap{position:absolute;left:0;bottom:0;width:100%;height:46px;background:rgba(3,85,163,.88);color:var(--white);font-size:18px;font-weight:500;padding-left:62px;display:flex;align-items:center}
.project .cap::before{content:"";position:absolute;left:0;top:0;width:46px;height:46px;background:var(--green);clip-path:polygon(0 60%,30% 100%,100% 0,60% 0,30% 55%)}
.dots{display:flex;gap:18px;left:540px}
.dots span{width:18px;height:18px;background:#7b8490}
.dots span:first-child{background:var(--blue)}
.partner h3{font-size:23px;font-weight:400;color:var(--blue);text-align:center}
.partner h3 span{color:var(--green)}
.pbox{position:absolute;height:113px;background:var(--white);box-shadow:0 2px 14px rgba(0,0,0,.12);display:flex;align-items:center;justify-content:center}
.pname{font-size:26px;font-weight:400;color:var(--ink)}
.cta{left:0;width:1200px;text-align:center;font-size:22px;line-height:33px;color:var(--blue)}
.cta span{color:var(--green)}
.footer-bg{top:3245px;height:290px;background:linear-gradient(180deg,#4e5a6b 0%,#2e3744 55%,#1f252e 100%)}
.foot-col h5{font-size:14px;font-weight:400;color:var(--green)}
.foot-col .rule{width:22px;height:2px;background:var(--white);margin:8px 0 14px}
.foot-col li{list-style:none;font-size:14px;color:var(--white);line-height:30px}
.foot-col li.on{color:var(--green)}
.soc li{display:flex;align-items:center;gap:10px;line-height:36px}
.soc i{width:24px;height:24px;border-radius:50%;border:2px solid var(--blue-mid);display:inline-block}
.contact li{display:flex;align-items:center;gap:14px;font-size:13px;line-height:34px}
.copy{top:3535px;height:44px;background:var(--green);color:var(--white);font-size:13px;display:flex;align-items:center;justify-content:center}
</style>
</head>
<body>
<div class="page">

  <div class="band hero-bg" role="img" aria-label="Aerial photograph of a brick medical office plaza with a parking lot and trees"></div>
  <div class="band hero-shade"></div>
  <div class="band" style="top:0;height:120px;background:linear-gradient(180deg,rgba(255,255,255,.85),rgba(255,255,255,0))"></div>

  <div class="abs topbar" style="left:143px;top:22px">
    <svg width="20" height="20" viewBox="0 0 24 24" fill="none" stroke="#0355a3" stroke-width="1.8"><path d="M5 3h4l2 5-2.5 1.5a12 12 0 0 0 6 6L16 13l5 2v4a2 2 0 0 1-2 2A17 17 0 0 1 3 5a2 2 0 0 1 2-2z"/></svg>
    <span>555.410.2288</span>
  </div>
  <div class="abs topbar" style="right:140px;top:22px">
    <svg width="20" height="18" viewBox="0 0 24 20" fill="none" stroke="#0355a3" stroke-width="1.8"><rect x="2" y="3" width="20" height="14"/><path d="M2 3l10 8 10-8"/></svg>
    <span>inquiry@velcoraso.com</span>
  </div>
  <nav class="nav">
    <a class="active" style="left:144px;top:72px">Home</a>
    <a style="left:242px;top:72px">About Us</a>
    <a style="left:810px;top:72px">Our Solutions</a>
    <a style="left:971px;top:72px">Contact Us</a>
  </nav>
  <div class="badge" style="left:458px;top:0;width:275px;height:196px;padding-bottom:30px">
    <div class="brand">VEL-CORA</div>
    <div class="brand-sub">SOLUTIONS</div>
  </div>
  <h1 class="abs hero-text">Vel-Cora Is An Investment Company That Focuses On Offering<br>Turn Key Solutions For Medical Professionals.</h1>

  <h2 class="title" style="top:630px">About Vel-Cora <span class="accent">Solutions</span></h2>
  <div class="title-rule" style="top:681px"></div>
  <div class="abs about-text" style="top:692px">
    <p>Vel-Cora is an investment company put together by a group of seasoned business professionals who have come together to combine decades of success in the real estate development, management, financing and medical services. The company will be a full service company offering turn key solutions for medical professionals.</p>
    <p>Vel-Cora will focus on providing a full range of services via a group of distinct companies to deliver newly emerging needs of the medical community.</p>
    <p>The end goal will be to create complete solutions for individuals in the medical community.</p>
  </div>
  <div class="btn" style="left:533px;top:857px;width:135px;padding-left:10px"><span class="mark"></span>Read More</div>

  <div class="band" style="top:963px;height:517px;background:var(--tint)"></div>
  <h2 class="title" style="top:1032px">Our <span class="accent">Solutions</span></h2>
  <div class="title-rule" style="top:1081px"></div>

  <div class="abs sol-col" style="left:143px;top:1136px">
    <div class="sol-icon">
      <svg width="40" height="40" viewBox="0 0 40 40" fill="none" stroke="#0355a3" stroke-width="2"><rect x="8" y="5" width="20" height="28"/><path d="M12 14h12M12 20h8M12 26h6"/><circle cx="29" cy="28" r="7" stroke="#8cc63f"/></svg>
    </div>
    <h3>Leasing Operations</h3>
    <p>Lorem ipsum dolor sit amet, consectetuer adipiscing elit, sed diam nonummy nibh euismod tincidunt ut laoreet dolore magna aliquam erat volutpat.</p>
    <a>Read More</a>
  </div>

  <div class="abs sol-mark" style="left:449px;top:1130px;width:278px;height:270px" role="img" aria-label="Large brand emblem filled with a photo of medical staff">
    <span class="brand" style="color:#fff;font-size:34px">VEL-CORA</span>
  </div>

  <div class="abs sol-col" style="left:771px;top:1136px">
    <div class="sol-icon">
      <svg width="40" height="40" viewBox="0 0 40 40" fill="none" stroke="#0355a3" stroke-width="2"><rect x="6" y="6" width="28" height="26"/><path d="M20 14l8 3v6c0 5-4 8-8 9-4-1-8-4-8-9v-6z" stroke="#8cc63f"/></svg>
    </div>
    <h3>Security Measures</h3>
    <p>Lorem ipsum dolor sit amet, consectetuer adipiscing elit, sed diam nonummy nibh euismod tincidunt ut laoreet dolore magna aliquam erat volutpat.</p>
    <a>Read More</a>
  </div>

  <h2 class="title" style="top:1555px">Our Management <span class="accent">Team</span></h2>
  <div class="title-rule" style="top:1605px"></div>

  <div class="abs member" style="left:146px;top:1716px">
    <div class="portrait" role="img" aria-label="Portrait of Wes Dalloran in a casual shirt"></div>
    <h4>Wes Dalloran</h4>
    <div class="firm">Firmstance</div>
  </div>
  <div class="abs member" style="left:473px;top:1716px">
    <div class="portrait" role="img" aria-label="Portrait of Dietmar Vellasquin in a shirt and tie"></div>
    <h4>Dietmar Vellasquin</h4>
    <div class="firm">GSH Dental Services</div>
  </div>
  <div class="abs member" style="left:800px;top:1716px">
    <div class="portrait" role="img" aria-label="Portrait of Dr. Gil Parish in a knit sweater"></div>
    <h4>Dr. Gil Parish</h4>
    <div class="firm">Firmstance</div>
  </div>

  <div class="band" style="top:2109px;height:621px;background:var(--tint)"></div>
  <h2 class="title" style="top:2185px">Upcoming <span class="accent">Projects</span></h2>
  <div class="title-rule" style="top:2234px"></div>

  <div class="project" style="left:143px;top:2263px">
    <div style="width:100%;height:100%;background:linear-gradient(120deg,#d9d6cf 0%,#b8b1a4 45%,#6f6a61 100%)" role="img" aria-label="Interior of a clinic reception area with a curved wooden desk and plants"></div>
    <div class="cap">Mt. Corwin Ridge Professional</div>
  </div>
  <div class="project" style="left:619px;top:2263px">
    <div style="width:100%;height:100%;background:linear-gradient(180deg,#a9c3d9 0%,#cdd8e0 40%,#7f8790 75%,#5b6066 100%)" role="img" aria-label="Rendering of a two-storey business park building with tenant signs"></div>
    <div class="cap">Holtmere Business Park</div>
  </div>

  <div class="abs dots" style="top:2630px"><span></span><span></span><span></span><span></span></div>

  <div class="abs partner" style="left:143px;top:2800px;width:445px"><h3>Our Construction <span>Partner</span></h3></div>
  <div class="abs partner" style="left:615px;top:2800px;width:445px"><h3>Our Equipment <span>Leasing Partner</span></h3></div>
  <div class="pbox" style="left:143px;top:2857px;width:445px">
    <div class="pname">318 Builders Inc.</div>
  </div>
  <div class="pbox" style="left:615px;top:2857px;width:445px">
    <div class="pname">Norvixa Equipment Leasing</div>
  </div>

  <p class="abs cta" style="top:3053px">Vel-Cora Will Focus On Providing A Full Range of Services Via A Group of Distinct<br>Companies To <span>Deliver Newly Emerging Needs of The Medical Community.</span></p>
  <div class="btn" style="left:494px;top:3139px;width:191px;padding-left:10px"><span class="mark"></span>Contact Us Today</div>

  <div class="band footer-bg" role="img" aria-label="Dusk city skyline with mountains behind"></div>

  <div class="abs foot-col" style="left:143px;top:3292px">
    <h5>Quick Links</h5><div class="rule"></div>
    <ul><li class="on">Home</li><li>About Us</li><li>Our Solutions</li><li>Contact Us</li></ul>
  </div>
  <div class="abs foot-col soc" style="left:297px;top:3292px">
    <h5>Social Media</h5><div class="rule"></div>
    <ul><li><i></i>Friendwall</li><li><i></i>Chirpline</li><li><i></i>Worknet</li></ul>
  </div>
  <div class="badge" style="left:458px;top:3245px;width:275px;height:196px;padding-bottom:26px">
    <div class="brand">VEL-CORA</div>
    <div class="brand-sub">SOLUTIONS</div>
  </div>
  <div class="abs foot-col contact" style="left:771px;top:3292px">
    <h5>Contact Details</h5><div class="rule"></div>
    <ul>
      <li><svg width="16" height="20" viewBox="0 0 16 20"><path d="M8 0a7 7 0 0 0-7 7c0 5 7 13 7 13s7-8 7-13a7 7 0 0 0-7-7z" fill="#8cc63f"/><circle cx="8" cy="7" r="2.5" fill="#2e3744"/></svg>Street Name, City Name, State Zipcode</li>
      <li><svg width="18" height="18" viewBox="0 0 24 24" fill="none" stroke="#8cc63f" stroke-width="2"><path d="M5 3h4l2 5-2.5 1.5a12 12 0 0 0 6 6L16 13l5 2v4a2 2 0 0 1-2 2A17 17 0 0 1 3 5a2 2 0 0 1 2-2z"/></svg>Call Us : 555.410.7890</li>
      <li><svg width="18" height="16" viewBox="0 0 24 20" fill="none" stroke="#8cc63f" stroke-width="2"><rect x="2" y="3" width="20" height="14"/><path d="M2 3l10 8 10-8"/></svg>Email Us: inquiry@velcoraso.com</li>
    </ul>
  </div>

  <div class="band copy">Copyright © 2020 Vel-Cora Solutions. All Rights Reserved.</div>
</div>
</body>
</html>
```